Veldmark Supplies Business Card

Professional business card that stand out to our potential customers. Front and back with clean modern design

Industry/Entity Type

Oil and gas

Contact Information for Business Card

Name, address, website , office phone and cell number

Requirements
Must have
• Editable files for each employee

```html
<!DOCTYPE html>
<html lang="en">
<head>
<meta charset="utf-8">
<title>Veldmark Supplies Business Card</title>
<link href="https://fonts.googleapis.com/css2?family=Montserrat:wght@400;500;700;800&display=swap" rel="stylesheet">
<style>
  :root {
    --brand-red: #ec1f27;
    --brand-blue: #0fb0d3;
    --ink: #1b1b1b;
    --paper: #ffffff;
    --backdrop: #d9d9d9;
  }
  * { box-sizing: border-box; margin: 0; padding: 0; }
  html, body { width: 1200px; height: 856px; overflow: hidden; }
  body {
    background: var(--backdrop);
    font-family: "Montserrat", Arial, sans-serif;
    position: relative;
  }
  .card {
    position: absolute;
    top: 258px;
    width: 540px;
    height: 340px;
    overflow: hidden;
    box-shadow: 0 10px 26px rgba(0,0,0,0.28);
  }
  .card-front { left: 40px; background: var(--paper); }
  .card-back { left: 620px; background: var(--brand-red); }

  /* front */
  .front-rules, .front-band { position: absolute; left: 0; top: 0; width: 540px; height: 340px; }
  .front-brand {
    position: absolute;
    left: 34px;
    top: 176px;
    width: 150px;
    display: flex;
    align-items: center;
    gap: 10px;
  }
  .brand-mark { width: 22px; height: 22px; background: var(--brand-blue); flex: none; }
  .brand-name {
    font-weight: 800;
    font-size: 19px;
    line-height: 1.15;
    letter-spacing: 0.5px;
    color: var(--brand-red);
    text-transform: uppercase;
  }
  .front-brand .brand-name { width: 110px; }
  .contact {
    position: absolute;
    left: 262px;
    top: 52px;
    width: 260px;
    color: var(--ink);
  }
  .contact-name {
    font-weight: 800;
    font-size: 22px;
    color: var(--brand-red);
    letter-spacing: 0.5px;
    text-transform: uppercase;
    white-space: nowrap;
  }
  .contact-title { font-size: 12.5px; font-weight: 500; margin-top: 2px; }
  .contact-address { font-size: 12.5px; line-height: 1.4; margin-top: 14px; }
  .contact-list { list-style: none; margin-top: 12px; }
  .contact-list li {
    display: flex;
    align-items: center;
    gap: 8px;
    font-size: 12.5px;
    line-height: 1.3;
    margin-bottom: 6px;
    white-space: nowrap;
  }
  .contact-icon {
    width: 17px; height: 17px;
    background: var(--brand-red);
    display: flex; align-items: center; justify-content: center;
    flex: none;
  }
  .contact-icon svg { width: 11px; height: 11px; }
  .web-accent { color: var(--brand-red); }

  /* back */
  .back-brand {
    position: absolute;
    inset: 0;
    display: flex;
    align-items: center;
    justify-content: center;
    gap: 14px;
  }
  .back-brand .brand-mark { width: 30px; height: 30px; }
  .back-brand .brand-name { color: var(--paper); font-size: 30px; }
</style>
</head>
<body>

<section class="card card-front" aria-label="Business card front">
  <svg class="front-rules" viewBox="0 0 540 340" aria-hidden="true">
    <line x1="204" y1="118" x2="204" y2="250" stroke="var(--brand-blue)" stroke-width="1.2"/>
    <line x1="218" y1="132" x2="218" y2="236" stroke="var(--brand-red)" stroke-width="1.2"/>
    <line x1="232" y1="146" x2="232" y2="222" stroke="var(--brand-red)" stroke-width="1.2"/>
  </svg>
  <svg class="front-band" viewBox="0 0 540 340" aria-hidden="true">
    <polygon points="0,326 318,326 310,340 0,340" fill="var(--brand-blue)"/>
    <polygon points="326,312 540,312 540,340 316,340" fill="var(--brand-red)"/>
  </svg>

  <div class="front-brand">
    <span class="brand-mark"></span>
    <span class="brand-name">Veldmark Supplies</span>
  </div>

  <div class="contact">
    <h1 class="contact-name">Dorran Halvik</h1>
    <p class="contact-title">President</p>
    <p class="contact-address">482 Quarry Ridge Rd, Ste<br>210, Midland, TX 79705</p>
    <ul class="contact-list">
      <li>
        <span class="contact-icon"><svg viewBox="0 0 12 12"><path d="M3 1 L5 3.5 L4 5 Q5 7 7 8 L8.5 7 L11 9 L9.5 11 Q4 10.5 1 3 Z" fill="#fff"/></svg></span>
        432-555-0148
      </li>
      <li>
        <span class="contact-icon"><svg viewBox="0 0 12 12"><rect x="3" y="0.5" width="6" height="11" rx="1" fill="none" stroke="#fff" stroke-width="1.2"/><circle cx="6" cy="9.5" r="0.7" fill="#fff"/></svg></span>
        432-555-0193
      </li>
      <li>
        <span class="contact-icon"><svg viewBox="0 0 12 12"><rect x="0.8" y="2.5" width="10.4" height="7" fill="none" stroke="#fff" stroke-width="1.1"/><path d="M0.8 2.5 L6 6.5 L11.2 2.5" fill="none" stroke="#fff" stroke-width="1.1"/></svg></span>
        info@veldmarksupplies.com
      </li>
      <li>
        <span class="contact-icon"><svg viewBox="0 0 12 12"><circle cx="6" cy="6" r="5" fill="none" stroke="#fff" stroke-width="1.1"/><ellipse cx="6" cy="6" rx="2.2" ry="5" fill="none" stroke="#fff" stroke-width="1"/><line x1="1" y1="6" x2="11" y2="6" stroke="#fff" stroke-width="1"/></svg></span>
        <span>www.<span class="web-accent">veldmarksupplies</span>.com</span>
      </li>
    </ul>
  </div>
</section>

<section class="card card-back" aria-label="Business card back">
  <div class="back-brand">
    <span class="brand-mark"></span>
    <span class="brand-name">Veldmark Supplies</span>
  </div>
</section>

</body>
</html>
```